Birch Hauling Business Card Design Project

We need a new company business card. We provide professional timber harvesting (logging) and forest management services. I'm open to any creative design. Most company caps and shirts are navy blue and Light grey. Logo does not necessarily have to contain those colors. Logo containing picture of logging equipment, log truck, trees, or logs are acceptable. Be creative. Final logo should communicate our company's pride and professionalism in the East Texas Timber Industry.
Updates

Target Market(s)

Timber owners, sawmills, and forestry professionals

Industry/Entity Type

Business

Requirements
Must have
• Must have Contact Info.
Phone: 936-402-5917
address: PO Box 4830
New Waverly, Tx 77358
www.jmbirchhauling.example
jmbirchhauling@mailbox.example
Owner: Jared Marsh

Or design must leave room for this info.

```html
<!DOCTYPE html>
<html lang="en">
<head>
<meta charset="utf-8">
<title>Birch Hauling Business Card</title>
<link rel="stylesheet" href="https://fonts.googleapis.com/css2?family=Ubuntu:wght@700&family=Oswald:wght@600&family=Exo+2:wght@400&display=swap">
<style>
  :root {
    --backdrop: #ddd6cb;
    --card-white: #ffffff;
    --card-fade: #eceded;
    --accent-yellow: #fbb52a;
    --ink-dark: #2b2b2b;
    --ink-grey: #6b6b6b;
    --rule-grey: #c9c9c9;
  }
  * { box-sizing: border-box; margin: 0; padding: 0; }
  html, body { width: 1200px; height: 1018px; overflow: hidden; }
  body { background: var(--backdrop); position: relative; font-family: "Exo 2", sans-serif; }

  .card {
    position: absolute; left: 210px; width: 780px; height: 446px;
    box-shadow: 0 10px 26px rgba(60, 45, 25, 0.28);
    overflow: hidden;
  }
  .card--front { top: 42px; background: linear-gradient(135deg, var(--card-white) 40%, var(--card-fade) 100%); }
  .card--back { top: 530px; background: var(--accent-yellow); }

  .card__side-panel {
    position: absolute; top: 0; right: 0; width: 140px; height: 100%;
    border-left: 1px solid var(--rule-grey);
    background: linear-gradient(180deg, #f4f4f4, #e6e7e7);
  }

  .brand { position: absolute; left: 58px; top: 62px; display: flex; align-items: center; gap: 26px; }
  .brand__mark { width: 84px; height: 84px; border-radius: 50%; background: var(--accent-yellow); }
  .brand__name {
    font-family: "Ubuntu", sans-serif; font-weight: 700; color: var(--ink-grey);
    font-size: 34px; line-height: 1.1;
  }

  .accent-rule { position: absolute; left: 0; top: 186px; width: 560px; height: 3px; background: var(--accent-yellow); }

  .person { position: absolute; left: 58px; top: 212px; }
  .person__name { font-family: "Oswald", sans-serif; font-weight: 600; font-size: 36px; letter-spacing: 1px; color: var(--ink-dark); line-height: 1.1; }
  .person__title { font-size: 14px; letter-spacing: 2px; color: var(--ink-dark); margin-top: 4px; }

  .contact-rule { position: absolute; left: 58px; top: 302px; width: 560px; height: 1px; background: var(--rule-grey); }

  .contacts {
    position: absolute; left: 58px; top: 324px; width: 560px;
    display: grid; grid-template-columns: 190px 1fr; row-gap: 14px;
    font-size: 15px; color: var(--ink-dark); letter-spacing: 0.5px;
  }
  .contacts__item { display: flex; align-items: center; gap: 10px; white-space: nowrap; }
  .contacts__item--wide { grid-column: 1 / span 2; }
  .contacts__icon { width: 15px; height: 15px; flex: none; fill: var(--ink-dark); }
  .contacts__icon--line { fill: none; stroke: var(--ink-dark); }
</style>
</head>
<body>
  <section class="card card--front" aria-label="Business card front">
    <div class="brand">
      <div class="brand__mark"></div>
      <div class="brand__name">Jared Marsh<br>Birch Hauling</div>
    </div>
    <div class="accent-rule"></div>

    <div class="person">
      <div class="person__name">DALE HARPER</div>
      <div class="person__title">GENERAL MANAGER</div>
    </div>

    <div class="contact-rule"></div>

    <div class="contacts">
      <div class="contacts__item">
        <svg class="contacts__icon" viewBox="0 0 16 16" aria-hidden="true"><path d="M3 1l3 3-1.6 2a9 9 0 0 0 5.6 5.6L12 10l3 3-2 2C7 15 1 9 1 3z"/></svg>
        555-555-0142
      </div>
      <div class="contacts__item">
        <svg class="contacts__icon" viewBox="0 0 16 16" aria-hidden="true"><path d="M1 3h14v10H1z M2 4.2v.6l6 4 6-4v-.6z" fill-rule="evenodd"/></svg>
        jmbirchhauling@mailbox.example
      </div>
      <div class="contacts__item">
        <svg class="contacts__icon" viewBox="0 0 16 16" aria-hidden="true"><path d="M4 1h8v14H4z M5.5 2.5v9h5v-9z" fill-rule="evenodd"/></svg>
        555-555-0187
      </div>
      <div class="contacts__item">
        <svg class="contacts__icon contacts__icon--line" viewBox="0 0 16 16" aria-hidden="true"><circle cx="8" cy="8" r="7" stroke-width="1.5"/><path d="M1 8h14M8 1c-3 3-3 11 0 14M8 1c3 3 3 11 0 14" stroke-width="1.2"/></svg>
        www.jmbirchhauling.example
      </div>
      <div class="contacts__item contacts__item--wide">
        PO Box 4830, Cedar Hollow, TX 00000
      </div>
    </div>

    <div class="card__side-panel"></div>
  </section>

  <section class="card card--back" aria-label="Business card back"></section>
</body>
</html>
```